Etiketten-Design für Gin
Zielgruppe
Destillieren von GIN (BrunoLIK) / Zielgruppe alle die GIN Lieben :)
Aufgabenstellung
die Grunddatei besteht schon im AI Format, allerdings möchten wir gerne die Highlights in Kupfer haben wie Schrift und Holzfässer, gerne auch eigene Bilder entwerfen. Lediglich das BrunoLIK Logo (Kopf) sollte erhalten bleiben. Bitte die Datei so anlegen das die Highlights in Kupfer gedruckt (Siebdruck) werden können. Transparentes Etikett wäre super! Bei Fragen einfach melden :)

```html
<!DOCTYPE html>
<html lang="de">
<head>
<meta charset="utf-8">
<title>Anton Barrel Aged Gin – Etikett</title>
<link href="https://fonts.googleapis.com/css2?family=Raleway:wght@300;400&display=swap" rel="stylesheet">
<style>
  :root {
    --page-bg: #e9ecec;
    --label-grey: #7d7d7d;
    --label-grey-light: #a2a2a2;
    --label-grey-dark: #6a6a6a;
    --copper: #e08a63;
    --copper-light: #f3b598;
    --label-white: #eeeeee;
  }
  * { margin: 0; padding: 0; box-sizing: border-box; }
  html, body { width: 1020px; height: 1200px; overflow: hidden; }
  body {
    background: var(--page-bg);
    font-family: "Raleway", "Helvetica Neue", Arial, sans-serif;
    position: relative;
  }
  .label {
    position: absolute;
    left: 60px; top: 147px;
    width: 900px; height: 906px;
    background: radial-gradient(ellipse at 50% 45%, var(--label-grey-light) 0%, var(--label-grey) 55%, var(--label-grey-dark) 100%);
  }
  .label-frame {
    position: absolute;
    inset: 10px;
    border: 2px solid var(--copper);
  }
  .portrait-area {
    position: absolute;
    left: 245px; top: 91px;
    width: 464px; height: 470px;
    border-radius: 48% 48% 44% 44%;
    background: radial-gradient(ellipse at 50% 50%, #d9c3b8 0%, #c98e74 45%, rgba(125,125,125,0) 72%);
  }
  .product-name {
    position: absolute;
    left: 0; right: 0; top: 570px;
    text-align: center;
    font-weight: 300;
    font-size: 150px;
    line-height: 1;
    color: var(--label-white);
    letter-spacing: 2px;
  }
  .product-type {
    position: absolute;
    left: 0; right: 0; top: 772px;
    text-align: center;
    font-weight: 300;
    font-size: 35px;
    color: var(--copper);
  }
  .spec {
    position: absolute;
    top: 846px;
    font-weight: 300;
    font-size: 34px;
    color: var(--label-white);
  }
  .spec-abv { left: 40px; }
  .spec-volume { right: 40px; }
</style>
</head>
<body>
  <section class="label">
    <div class="label-frame"></div>
    <div class="portrait-area" role="img" aria-label="Copper and white sketched portrait illustration of the brand's namesake"></div>
    <h1 class="product-name">Anton</h1>
    <p class="product-type">Barrel Aged Gin</p>
    <p class="spec spec-abv">45% vol.</p>
    <p class="spec spec-volume">0,5 l</p>
  </section>
</body>
</html>
```